Business Card for Vorla Parts Wholesale supplier

Hi There! I need a new business card for our company. We are specialized in selling Vorla parts, mostly we sell new LCD screens for Zelnar and Drelks. I would like to see that back in the design.

You can find the colors and logo's on our website: www.hartuvo.nl

Industry/Entity Type

Business

Contact Information for Business Card

My Details:
Tobias Lindqvist

Phone: 0031687203316
E-mail: Tobias@hartuvo.nl

Slogan: "Because Quality Matters"

Font styles to use
Sans Serif

Colors

Designer to choose colors to be used in the design.

Requirements
Must have
• A Black backside with the Hartuvo logo on it. The front side should be clean with only my contact details.
• But I'm also open for something really different or awesome!
Nice to have
• Remember that we are in the parts & repairing industry, So i'll be handing those business cards mainly to repair companies. Maybe you can do something with that thought :)

```html
<!DOCTYPE html>
<html lang="en">
<head>
<meta charset="utf-8">
<title>Hartuvo – Business Card</title>
<link rel="stylesheet" href="https://fonts.googleapis.com/css2?family=Roboto:wght@400;500;700&display=swap">
<style>
  :root {
    --page: #e6e6e6;
    --card-dark: #1e1e1e;
    --card-dark-deep: #141414;
    --card-light: #f7f7f7;
    --band: #1b1b1b;
    --accent: #e8661c;
    --ink: #1c1c1c;
    --ink-soft: #333333;
    --white: #ffffff;
  }
  * { box-sizing: border-box; margin: 0; padding: 0; }
  html, body {
    width: 1200px; height: 576px; overflow: hidden;
    background: var(--page);
    font-family: "Roboto", Arial, sans-serif;
  }
  .canvas { position: relative; width: 1200px; height: 576px; }

  .card {
    position: absolute; top: 138px;
    width: 484px; height: 294px;
    border-radius: 14px; overflow: hidden;
  }

  /* Back side */
  .card--back { left: 82px; background: var(--card-dark); }
  .card--back .backdrop {
    position: absolute; inset: 0;
    background:
      linear-gradient(160deg, #2a2a2a 0%, #222 35%, #1a1a1a 60%, var(--card-dark-deep) 100%);
  }
  .card--back .wordmark {
    position: absolute; left: 104px; top: 122px;
    display: flex; align-items: center; gap: 14px;
  }
  .wordmark-dot {
    width: 40px; height: 40px; border-radius: 50%;
    background: var(--accent);
  }
  .card--back .wordmark-name {
    font-size: 48px; font-weight: 500; color: var(--white);
    letter-spacing: 0.5px; line-height: 1;
  }

  /* Front side */
  .card--front { left: 602px; background: var(--card-light); }
  .side-band {
    position: absolute; left: 0; top: 0; bottom: 0; width: 40px;
    background: var(--band);
  }
  .side-stripe {
    position: absolute; left: 40px; top: 0; bottom: 0; width: 5px;
    background: var(--accent);
  }
  .card--front .wordmark {
    position: absolute; right: 36px; top: 36px;
    display: flex; align-items: center; gap: 12px;
  }
  .card--front .wordmark-dot { width: 36px; height: 36px; }
  .card--front .wordmark-name {
    font-size: 42px; font-weight: 500; color: var(--ink);
    letter-spacing: 0.5px; line-height: 1;
  }
  .contact-block { position: absolute; left: 61px; top: 204px; }
  .person-name {
    font-size: 18px; font-weight: 700; color: var(--accent); line-height: 1.2;
  }
  .person-role {
    margin-top: 3px; font-size: 11px; color: var(--ink-soft);
  }
  .contact-row {
    margin-top: 16px; display: flex; align-items: center; gap: 7px;
    font-size: 12px; color: var(--ink);
  }
  .contact-item { display: flex; align-items: center; gap: 4px; }
  .contact-item svg { width: 11px; height: 11px; fill: var(--accent); }
</style>
</head>
<body>
<main class="canvas">

  <section class="card card--back" aria-label="Card back">
    <div class="backdrop" role="img" aria-label="Dark close-up photo of a smartphone with a cracked screen"></div>
    <div class="wordmark">
      <span class="wordmark-dot"></span>
      <span class="wordmark-name">hartuvo</span>
    </div>
  </section>

  <section class="card card--front" aria-label="Card front">
    <div class="side-band"></div>
    <div class="side-stripe"></div>
    <div class="wordmark">
      <span class="wordmark-dot"></span>
      <span class="wordmark-name">hartuvo</span>
    </div>
    <div class="contact-block">
      <p class="person-name">Tobias Lindqvist</p>
      <p class="person-role">Managing Director</p>
      <div class="contact-row">
        <span class="contact-item">
          <svg viewBox="0 0 24 24" aria-hidden="true"><path d="M6.6 10.8a15.1 15.1 0 0 0 6.6 6.6l2.2-2.2c.3-.3.7-.4 1-.2 1.1.4 2.3.6 3.6.6.6 0 1 .4 1 1V20c0 .6-.4 1-1 1A17 17 0 0 1 3 4c0-.6.4-1 1-1h3.5c.6 0 1 .4 1 1 0 1.3.2 2.5.6 3.6.1.3 0 .7-.2 1z"/></svg>
          0031687203316
        </span>
        <span class="contact-item">
          <svg viewBox="0 0 24 24" aria-hidden="true"><path d="M2 5h20v14H2z M2 5l10 8 10-8" fill="var(--accent)"/><path d="M3 6l9 7 9-7" fill="none" stroke="#fff" stroke-width="1.6"/></svg>
          Tobias@hartuvo.nl
        </span>
        <span class="contact-item">
          <svg viewBox="0 0 24 24" aria-hidden="true"><circle cx="12" cy="12" r="10"/><path d="M2 12h20M12 2c3 3 3 17 0 20M12 2c-3 3-3 17 0 20" fill="none" stroke="#fff" stroke-width="1.4"/></svg>
          www.hartuvo.nl
        </span>
      </div>
    </div>
  </section>

</main>
</body>
</html>
```